Camp Thornbriar Day Camp Brochure

I need someone to design a brochure for our day camp. It will be 8.5 x 11 inch paper folded horizontally. Looking for a fun, clean design. I sent several pictures, not all of them have to be used. The brochure will be mailed out to former day campers and used at events to help us market our program. A colorful brochure would be nice. I would like the cover page to be portrait along with the two inside pages. The back cover will need to be landscape format.

Target Market(s)

Parents

Colors

Designer to choose colors to be used in the design.

Requirements
Must have
• All information provided. Great design on the inside pages

```html
<!DOCTYPE html>
<html lang="en">
<head>
<meta charset="utf-8">
<title>Camp Thornbriar Day Camp 2019 Brochure</title>
<link href="https://fonts.googleapis.com/css2?family=Montserrat:wght@400;500;600;700;800&display=swap" rel="stylesheet">
<style>
:root{
  --green:#2f7d1e;
  --green-dark:#22601a;
  --red:#7c1511;
  --red-light:#93241c;
  --white:#ffffff;
  --ink:#2a2a2a;
  --stage:#2d2d2d;
  --grey:#ececec;
}
*{box-sizing:border-box;margin:0;padding:0}
html,body{width:840px;height:1200px;overflow:hidden}
body{background:var(--stage);font-family:"Montserrat",sans-serif;color:var(--ink);position:relative}
.spread{position:absolute;left:0;width:840px;height:543px;display:flex}
.spread-outer{top:38px}
.spread-inner{top:619px}
.page{position:relative;width:420px;height:543px;overflow:hidden;background:var(--white)}
.photo{position:absolute}
.web{position:absolute;left:0;right:0;bottom:0;height:46px;background:var(--green);color:var(--white);
  display:flex;align-items:center;justify-content:center;gap:6px;font-size:10px;font-weight:500;letter-spacing:.3px}
.web svg{width:10px;height:10px}

/* back cover */
.mailer{position:absolute;left:0;top:0;width:420px;height:180px;background:var(--white)}
.return-address{position:absolute;left:40px;top:82px;font-size:7.5px;line-height:1.35;color:#444}
.return-address .org{font-size:13px;font-weight:800;letter-spacing:.5px;color:var(--ink);margin-bottom:8px}
.resident{position:absolute;left:200px;top:112px;font-size:6.5px;font-weight:600;letter-spacing:.3px;color:#444}
.indicia{position:absolute;right:38px;top:34px;width:52px;height:42px;border:1px solid #666;font-size:5px;line-height:1.3;
  padding:4px;text-align:center;color:#444}

/* front cover */
.cover-title{position:absolute;left:118px;top:318px;width:290px;padding:12px 18px;background:rgba(38,38,38,.88);color:var(--white)}
.cover-title .small{font-size:16px;font-weight:500}
.cover-title .big{font-size:25px;font-weight:700;line-height:1.1}
.cover-title::after{content:"";position:absolute;left:0;bottom:-6px;width:290px;height:3px;background:var(--green)}

/* inside pages */
.page-bg{position:absolute;inset:0}
.intro{position:absolute;left:26px;top:26px;width:372px;color:var(--white)}
.intro .lead{font-size:11.5px;font-weight:700;line-height:1.3}
.intro .lead strong{font-size:17px;font-weight:800}
.intro .body{font-size:8.6px;line-height:1.35;margin-top:9px;font-weight:500}
.intro .open{font-size:9.3px;font-weight:700;line-height:1.35;margin-top:9px}
.intro .note{font-size:7px;line-height:1.35;margin-top:8px}
.price-list{margin-top:7px;display:flex;flex-direction:column;gap:4px}
.price-row{display:flex;align-items:center;gap:6px}
.price-age{width:140px;background:var(--green);color:var(--white);font-size:9.5px;font-weight:700;padding:3px 10px;border:1px solid rgba(255,255,255,.5)}
.price-cost{width:52px;background:var(--white);color:var(--red);font-size:10px;font-weight:800;text-align:center;padding:2px 0}
.camp-photo{position:absolute;left:30px;width:300px;border:3px solid var(--white)}

.section-title{font-size:15px;font-weight:800;color:var(--white);position:relative;margin-bottom:12px}
.section-title::after{content:"";position:absolute;left:0;bottom:-5px;width:22px;height:3px;border-radius:2px;background:var(--green)}
.inside-right{position:absolute;left:26px;top:26px;width:370px;color:var(--white)}
.stop{display:flex;justify-content:space-between;align-items:center;margin-bottom:4px}
.stop-name{width:170px;font-size:8px;font-weight:600;border:1px solid rgba(255,255,255,.6);border-radius:3px;padding:3px 8px}
.stop-time{width:120px;background:var(--green);font-size:8.5px;font-weight:700;text-align:center;padding:3px 0;border-radius:3px}
.discounts{margin-top:18px}
.discount{font-size:7.5px;line-height:1.35;margin-bottom:2px}
.discount b{color:#5fbf45;font-weight:700}
.weeks{margin-top:16px;display:grid;grid-template-columns:1fr 1fr;column-gap:14px;row-gap:4px}
.week{display:flex;align-items:center;gap:4px}
.week-label{width:54px;font-size:8.5px;font-weight:700;border:1px solid rgba(255,255,255,.6);border-radius:3px;padding:2px 6px}
.week-dates{flex:1;background:var(--white);color:var(--ink);font-size:8.5px;font-weight:700;border-radius:3px;padding:2px 8px}
.register{position:absolute;left:60px;right:60px;top:430px;text-align:center}
.register .call{font-size:11px;font-weight:700;color:#444}
.register .pill{margin:4px 0;background:var(--green);color:var(--white);font-size:17px;font-weight:800;padding:6px 0;border-radius:20px;position:relative}
.register .pill svg{position:absolute;right:16px;top:9px;width:12px;height:14px}
.register .limit{font-size:11px;font-weight:700;color:#444}
</style>
</head>
<body>

<section class="spread spread-outer" aria-label="Outer spread: back cover and front cover">
  <article class="page back-cover">
    <div class="photo" role="img" aria-label="Photo of a smiling child eating watermelon among the trees"
      style="left:0;top:180px;width:420px;height:317px;background:linear-gradient(160deg,#5d7a52 0%,#a4a68a 35%,#d9b79a 55%,#c9c5bb 80%,#8a8f7e 100%)"></div>
    <div class="mailer">
      <div class="return-address">
        <div class="org">CAMP THORNBRIAR</div>
        PO Box 4821<br>Millbrook, AR<br>501-555-0148<br>office@campthornbriar.org
      </div>
      <div class="resident">OR CURRENT RESIDENT</div>
      <div class="indicia">Nonprofit Org<br>US Postage<br>Paid<br>Millbrook AR<br>Permit 70</div>
    </div>
    <div class="web">
      <svg viewBox="0 0 10 10" fill="none" stroke="#fff" stroke-width=".9"><circle cx="5" cy="5" r="4.3"/><ellipse cx="5" cy="5" rx="1.8" ry="4.3"/><line x1=".7" y1="5" x2="9.3" y2="5"/></svg>
      www.campthornbriar.org
    </div>
  </article>

  <article class="page front-cover">
    <div class="photo" role="img" aria-label="Photo of a girl in a helmet riding a horse in the woods"
      style="left:0;top:0;width:420px;height:497px;background:linear-gradient(170deg,#4f6b45 0%,#7b8e68 30%,#c4534f 50%,#c9b89a 70%,#dcd3c2 100%)"></div>
    <div class="cover-title">
      <div class="small">Camp Thornbriar</div>
      <div class="big">Day Camp 2019</div>
    </div>
    <div class="web">
      <svg viewBox="0 0 10 10" fill="none" stroke="#fff" stroke-width=".9"><circle cx="5" cy="5" r="4.3"/><ellipse cx="5" cy="5" rx="1.8" ry="4.3"/><line x1=".7" y1="5" x2="9.3" y2="5"/></svg>
      www.campthornbriar.org
    </div>
  </article>
</section>

<section class="spread spread-inner" aria-label="Inside spread">
  <article class="page inside-left">
    <svg class="page-bg" viewBox="0 0 420 543" preserveAspectRatio="none" aria-hidden="true">
      <defs>
        <linearGradient id="redLeft" x1="0" y1="0" x2="1" y2="1">
          <stop offset="0" stop-color="#7c1511"/><stop offset="1" stop-color="#93241c"/>
        </linearGradient>
      </defs>
      <path d="M0 0H420V440C390 440 372 400 340 360C330 348 320 345 300 345H0Z" fill="url(#redLeft)"/>
      <path d="M0 522H380C400 522 410 510 420 495V503C410 518 400 530 380 530H0Z" fill="#2f7d1e"/>
    </svg>
    <div class="intro">
      <p class="lead"><strong>Since 1980,</strong> Camp Thornbriar has offered day camp. This summer, we have nine one-week sessions. Come to one session or all nine.</p>
      <p class="body">Each week our activities include swimming, horseback riding, Bible lessons, singing, arts and crafts, cookouts, hiking, and much more.</p>
      <p class="open">Day camp is open to all kids ages 5 and up. Costs are as follows for one session of day camp:</p>
      <div class="price-list">
        <div class="price-row"><span class="price-age">5-7 YEAR OLDS</span><span class="price-cost">$105</span></div>
        <div class="price-row"><span class="price-age">8 YEARS AND UP</span><span class="price-cost">$120</span></div>
      </div>
      <p class="note">For your convenience we run a bus in Millbrook each day to pick-up and drop-off campers. Please see the bus schedule below for locations and times. Campers may be dropped off and picked up at Thornbriar between 7:45 a.m. and 4:45 p.m. if you prefer.</p>
    </div>
    <div class="camp-photo" role="img" aria-label="Photo of a group of campers posing outdoors under trees"
      style="top:300px;height:100px;background:linear-gradient(120deg,#4e6a3f,#9aa677 40%,#d88fb0 65%,#7ea0c8)"></div>
    <div class="camp-photo" role="img" aria-label="Photo of campers and counselors sitting together on benches"
      style="top:400px;height:105px;background:linear-gradient(120deg,#8b6a4a,#d39a8a 40%,#e46fa3 60%,#b08867)"></div>
  </article>

  <article class="page inside-right-page">
    <svg class="page-bg" viewBox="0 0 420 543" preserveAspectRatio="none" aria-hidden="true">
      <defs>
        <linearGradient id="redRight" x1="0" y1="0" x2="1" y2="1">
          <stop offset="0" stop-color="#93241c"/><stop offset="1" stop-color="#6e100d"/>
        </linearGradient>
      </defs>
      <path d="M0 0H420V420C300 420 120 400 0 400Z" fill="url(#redRight)"/>
      <path d="M0 526H420V534H0Z" fill="#2f7d1e"/>
    </svg>
    <div class="inside-right">
      <h2 class="section-title">Bus Stop Schedule</h2>
      <div class="stop"><span class="stop-name">Grace Hill Chapel</span><span class="stop-time">7:15 a.m./5:30 p.m.</span></div>
      <div class="stop"><span class="stop-name">Oakdale Center</span><span class="stop-time">7:30 a.m./5:15 p.m.</span></div>
      <div class="stop"><span class="stop-name">Main Street Church</span><span class="stop-time">7:45 a.m./5:00 p.m.</span></div>

      <div class="discounts">
        <h2 class="section-title">Discounts</h2>
        <p class="discount"><b>Early Bird:</b> A $5 discount per session, per child is offered if the child is registered by May 1st.</p>
        <p class="discount"><b>Siblings:</b> $5 off per child for each session, per family.</p>
        <p class="discount"><b>Multi-Session:</b> $5 off per child, per session if you register for more than one session.</p>
      </div>

      <h2 class="section-title" style="margin-top:14px">Weeks</h2>
      <div class="weeks">
        <div class="week"><span class="week-label">Week 1:</span><span class="week-dates">June 3rd - 7th</span></div>
        <div class="week"><span class="week-label">Week 2:</span><span class="week-dates">June 10th - 14th</span></div>
        <div class="week"><span class="week-label">Week 3:</span><span class="week-dates">June 17th - 21st</span></div>
        <div class="week"><span class="week-label">Week 4:</span><span class="week-dates">June 24th - 28th</span></div>
        <div class="week"><span class="week-label">Week 5:</span><span class="week-dates">July 1st - 5th</span></div>
        <div class="week"><span class="week-label">Week 6:</span><span class="week-dates">July 8th - 12th</span></div>
        <div class="week"><span class="week-label">Week 7:</span><span class="week-dates">July 15th - 19th</span></div>
        <div class="week"><span class="week-label">Week 8:</span><span class="week-dates">July 22nd - 26th</span></div>
        <div class="week"><span class="week-label">Week 9:</span><span class="week-dates">July 29 - August 2nd</span></div>
      </div>
    </div>
    <div class="register">
      <p class="call">Register today at</p>
      <p class="pill">campthornbriar.org!
        <svg viewBox="0 0 12 14" aria-hidden="true"><path d="M1 1L1 11L4 8.5L6 13L8 12L6 7.8L10 7.8Z" fill="#fff" stroke="#2f7d1e" stroke-width=".6"/></svg>
      </p>
      <p class="limit">Spaces are limited</p>
    </div>
  </article>
</section>

</body>
</html>
```